Detail Shop Business card design

i need a business card design for my new detailing company called 'Brisk's Polish Works'. i want an all black and white design . simple, direct and to the point. i want the designer to choose a fitting font to match the logothe front should have logo, address, phone and email and the back side should have a slogan and text indicating that we offer services on anything including cars, trucks, motorcycles and RVs. slogan will read "we take pride in your ride"
maybe also very small on the back side the IG icon with Brisks_Polish_Works

phone 208.417.6352
address 3847 E Larkin Ave
Spokane WA 99214
email: BrisksPolish@mailvexo.com

Target Market(s)

all ages , auto enthusiasts

Industry/Entity Type

Automotive

Contact Information for Business Card

the front should have logo, address, phone and email and the back side should have a slogan and text indicating that we offer services on anything including cars, trucks, motorcycles and RVs. slogan will read "we take pride in your ride"

phone 208.417.6352
address 3847 E Larkin Ave
Spokane WA 99214

Colors
000000
ffffff

Requirements
Must have
• bold font and very simple design with good spacing
Nice to have
• anything creative from the designer indicating we service any types of vehicles
Should not have
• any colors ,

```html
<!DOCTYPE html>
<html lang="en">
<head>
<meta charset="utf-8">
<title>Brisk's Polish Works – Business Card</title>
<link rel="stylesheet" href="https://fonts.googleapis.com/css2?family=Roboto+Slab:wght@400;700&family=Oswald:wght@400;600&display=swap">
<style>
  :root {
    --page: #e9e9e7;
    --paper: #fbfbfb;
    --ink: #111111;
    --ink-soft: #3a3a3a;
    --ink-muted: #6a6a6a;
    --back-card: #4d4d4d;
    --band: #141414;
    --band-text: #f2f2f2;
    --rule: #c9c9c9;
  }
  * { box-sizing: border-box; margin: 0; padding: 0; }
  html, body {
    width: 1200px; height: 950px; overflow: hidden;
    background: var(--page);
  }
  .canvas { position: relative; width: 1200px; height: 950px; }
  .card {
    position: absolute; left: 250px; width: 700px; height: 400px;
    box-shadow: 0 6px 18px rgba(0,0,0,.18);
    overflow: hidden;
  }

  /* ---------- Front ---------- */
  .card-front { top: 50px; background: var(--paper); }
  .brand {
    position: absolute; left: 52px; top: 96px; width: 250px;
    display: flex; align-items: center; gap: 16px;
  }
  .brand-dot {
    flex: none; width: 54px; height: 54px; border-radius: 50%;
    border: 6px solid var(--ink);
  }
  .brand-name {
    font-family: "Roboto Slab", serif; font-weight: 700;
    font-size: 28px; line-height: 1.15; color: var(--ink);
    text-transform: uppercase;
  }
  .divider {
    position: absolute; left: 330px; top: 70px; width: 1px; height: 190px;
    background: var(--rule);
  }
  .contact {
    position: absolute; left: 362px; top: 62px; width: 310px;
    font-family: "Roboto Slab", serif; color: var(--ink-soft);
  }
  .contact-name { font-size: 22px; font-weight: 400; color: var(--ink); letter-spacing: .5px; }
  .contact-role { font-size: 14px; color: var(--ink-muted); margin-bottom: 16px; }
  .contact-address { font-size: 14px; line-height: 1.5; margin-bottom: 12px; }
  .contact-list { list-style: none; font-size: 14px; line-height: 1.75; }
  .contact-list li { display: flex; align-items: center; gap: 10px; white-space: nowrap; }
  .contact-list svg { width: 14px; height: 14px; flex: none; }

  .web-band { position: absolute; left: 0; bottom: 46px; width: 700px; height: 44px; }
  .web-band svg { position: absolute; inset: 0; }
  .web-url {
    position: absolute; inset: 0; display: flex; align-items: center; justify-content: center;
    font-family: "Roboto Slab", serif; font-size: 15px; font-weight: 700;
    letter-spacing: 7px; color: var(--band-text);
  }

  /* ---------- Back ---------- */
  .card-back { top: 500px; background: var(--back-card); }
  .vehicle-art {
    position: absolute; left: 330px; top: 70px; width: 330px; height: 250px;
    border-radius: 90px 110px 40px 40px;
    background: linear-gradient(100deg, #2a2a2a, #0d0d0d 60%, #242424);
  }
  .slogan-block { position: absolute; left: 44px; top: 110px; width: 250px; }
  .slogan {
    font-family: "Oswald", sans-serif; font-weight: 600; font-size: 30px;
    line-height: 1.15; color: var(--ink); text-transform: uppercase;
  }
  .slogan-rule { height: 2px; background: var(--ink); margin: 14px 0 12px; width: 240px; }
  .services {
    font-family: "Oswald", sans-serif; font-weight: 400; font-size: 15px;
    color: var(--ink); line-height: 1.4;
  }
</style>
</head>
<body>
<main class="canvas">

  <section class="card card-front" aria-label="Business card front">
    <div class="brand">
      <span class="brand-dot"></span>
      <span class="brand-name">Brisk's Polish Works</span>
    </div>

    <div class="divider"></div>

    <div class="contact">
      <p class="contact-name">DALE HARMON</p>
      <p class="contact-role">CEO/FOUNDER</p>
      <p class="contact-address">3847 E Larkin Ave<br>Spokane WA 99214</p>
      <ul class="contact-list">
        <li>
          <svg viewBox="0 0 14 14" aria-hidden="true"><path d="M3 1l2.5 3-1.3 1.5a8 8 0 0 0 4.3 4.3L10 8.5l3 2.5-1.5 2C6 13 1 8 1 2.5z" fill="#111"/></svg>
          208.417.6352
        </li>
        <li>
          <svg viewBox="0 0 14 14" aria-hidden="true"><rect x="3" y="1" width="8" height="12" rx="1.2" fill="none" stroke="#111" stroke-width="1.5"/><circle cx="7" cy="11" r=".8" fill="#111"/></svg>
          208.552.7190
        </li>
        <li>
          <svg viewBox="0 0 14 14" aria-hidden="true"><rect x="1" y="3" width="12" height="8" fill="#111"/><path d="M1 3l6 4.5L13 3" fill="none" stroke="#fbfbfb" stroke-width="1.2"/></svg>
          BrisksPolish@mailvexo.com
        </li>
      </ul>
    </div>

    <div class="web-band">
      <svg viewBox="0 0 700 44" preserveAspectRatio="none" aria-hidden="true">
        <polygon points="0,0 700,0 700,44 0,44 14,22" fill="#141414"/>
        <polygon points="700,0 686,22 700,44" fill="#fbfbfb"/>
        <polygon points="40,15 42.5,20 48,20 43.5,23.5 45.5,29 40,25.5 34.5,29 36.5,23.5 32,20 37.5,20" fill="#f2f2f2"/>
        <polygon points="660,15 662.5,20 668,20 663.5,23.5 665.5,29 660,25.5 654.5,29 656.5,23.5 652,20 657.5,20" fill="#f2f2f2"/>
      </svg>
      <span class="web-url">www.briskspolish.com</span>
    </div>
  </section>

  <section class="card card-back" aria-label="Business card back">
    <div class="vehicle-art" role="img" aria-label="Black silhouette illustration of a vintage hot rod"></div>
    <div class="slogan-block">
      <p class="slogan">We take pride in your ride</p>
      <div class="slogan-rule"></div>
      <p class="services">Services on anything including cars, trucks, motorcycles &amp; RVs</p>
    </div>
  </section>

</main>
</body>
</html>
```